Step and Repeat Backdrop for wedding reception photo booth

Would like to have a Step and Repeat Backdrop (8 foot high by 10 foot wide) that incorporates the wedding logo (attached) and the names Helen and Gavin. Background should be white, and wedding colors are burgundy and gold. Show me creativity :-) I have included some random samples.

```html
<!DOCTYPE html>
<html lang="en">
<head>
<meta charset="utf-8">
<title>Helen &amp; Gavin – Step and Repeat Backdrop</title>
<link rel="stylesheet" href="https://fonts.googleapis.com/css2?family=Cormorant+Garamond:wght@500;600&display=swap">
<style>
  :root {
    --page-bg: #ececee;
    --banner-bg: #ffffff;
    --repeat-rose: #c49090;
    --gold: #d89a2a;
    --gold-light: #f0bd3a;
    --gold-deep: #c47a28;
    --banner-edge: #d6d6d9;
  }
  html, body {
    margin: 0;
    padding: 0;
    width: 1200px;
    height: 1200px;
    overflow: hidden;
    background: var(--page-bg);
  }
  .backdrop {
    position: absolute;
    left: 50px;
    top: 160px;
    width: 1100px;
    height: 880px;
    box-sizing: border-box;
    padding: 20px 18px;
    background: var(--banner-bg);
    border: 1px solid var(--banner-edge);
    display: grid;
    grid-template-columns: repeat(8, 1fr);
    grid-template-rows: repeat(8, 1fr);
    overflow: hidden;
  }
  .repeat-mark {
    display: flex;
    align-items: center;
    justify-content: center;
    min-width: 0;
    font-family: "Cormorant Garamond", serif;
    font-weight: 500;
    font-size: 38px;
    color: var(--repeat-rose);
    letter-spacing: -1px;
  }
  .centrepiece {
    grid-column: 4 / 6;
    grid-row: 3 / 6;
    margin: 0 -22px;
    display: flex;
    flex-direction: column;
    align-items: center;
    justify-content: center;
    gap: 10px;
    min-width: 0;
  }
  .flourish {
    width: 290px;
    height: 44px;
    border-radius: 22px;
    background: linear-gradient(90deg, var(--gold-deep), var(--gold), var(--gold-light));
    opacity: 0.35;
  }
  .feature-monogram {
    font-family: "Cormorant Garamond", serif;
    font-weight: 600;
    font-size: 118px;
    line-height: 1;
    color: var(--gold);
    letter-spacing: -4px;
  }
  .couple-names {
    grid-column: 3 / 7;
    grid-row: 6 / 7;
    display: flex;
    align-items: center;
    justify-content: center;
    gap: 18px;
    min-width: 0;
    font-family: "Cormorant Garamond", serif;
    font-weight: 600;
    font-size: 40px;
    color: var(--gold);
  }
  .couple-names .name { letter-spacing: 0.5em; }
  .couple-names .name:first-child { margin-right: -0.5em; }
  .couple-names .name:last-child { margin-right: -0.5em; }
  .couple-names .divider {
    width: 38px;
    height: 38px;
    border: 3px solid var(--gold);
    border-radius: 50%;
    box-sizing: border-box;
    flex: none;
  }
</style>
</head>
<body>
  <main class="backdrop" aria-label="Step and repeat backdrop for Helen and Gavin">
    <div class="centrepiece">
      <div class="flourish" role="img" aria-label="Gold scroll flourish above the monogram"></div>
      <div class="feature-monogram">H&amp;G</div>
      <div class="flourish" role="img" aria-label="Gold scroll flourish below the monogram"></div>
    </div>
    <div class="couple-names">
      <span class="name">Helen</span>
      <span class="divider" aria-hidden="true"></span>
      <span class="name">Gavin</span>
    </div>

    <div class="repeat-mark">H&amp;G</div><div class="repeat-mark">H&amp;G</div><div class="repeat-mark">H&amp;G</div><div class="repeat-mark">H&amp;G</div><div class="repeat-mark">H&amp;G</div><div class="repeat-mark">H&amp;G</div>
    <div class="repeat-mark">H&amp;G</div><div class="repeat-mark">H&amp;G</div><div class="repeat-mark">H&amp;G</div><div class="repeat-mark">H&amp;G</div><div class="repeat-mark">H&amp;G</div><div class="repeat-mark">H&amp;G</div>
    <div class="repeat-mark">H&amp;G</div><div class="repeat-mark">H&amp;G</div><div class="repeat-mark">H&amp;G</div><div class="repeat-mark">H&amp;G</div><div class="repeat-mark">H&amp;G</div><div class="repeat-mark">H&amp;G</div>
    <div class="repeat-mark">H&amp;G</div><div class="repeat-mark">H&amp;G</div><div class="repeat-mark">H&amp;G</div><div class="repeat-mark">H&amp;G</div><div class="repeat-mark">H&amp;G</div><div class="repeat-mark">H&amp;G</div>
    <div class="repeat-mark">H&amp;G</div><div class="repeat-mark">H&amp;G</div><div class="repeat-mark">H&amp;G</div><div class="repeat-mark">H&amp;G</div><div class="repeat-mark">H&amp;G</div><div class="repeat-mark">H&amp;G</div>
    <div class="repeat-mark">H&amp;G</div><div class="repeat-mark">H&amp;G</div><div class="repeat-mark">H&amp;G</div><div class="repeat-mark">H&amp;G</div><div class="repeat-mark">H&amp;G</div><div class="repeat-mark">H&amp;G</div>
    <div class="repeat-mark">H&amp;G</div><div class="repeat-mark">H&amp;G</div><div class="repeat-mark">H&amp;G</div><div class="repeat-mark">H&amp;G</div><div class="repeat-mark">H&amp;G</div><div class="repeat-mark">H&amp;G</div>
    <div class="repeat-mark">H&amp;G</div><div class="repeat-mark">H&amp;G</div><div class="repeat-mark">H&amp;G</div><div class="repeat-mark">H&amp;G</div><div class="repeat-mark">H&amp;G</div><div class="repeat-mark">H&amp;G</div>
    <div class="repeat-mark">H&amp;G</div><div class="repeat-mark">H&amp;G</div><div class="repeat-mark">H&amp;G</div><div class="repeat-mark">H&amp;G</div><div class="repeat-mark">H&amp;G</div><div class="repeat-mark">H&amp;G</div>
  </main>
</body>
</html>
```